Business card por a urban DJ, up scale audience target

Need a sober design, modern, conservative colors but i can consider some options, y play rnb, hip hop, EDM and top40.

Business card for contact and personal info, double sided, use logo attrached please; im 42 so i need a card acording to my age an target audience.

Target Market(s)

Adult people, up scale audience

Industry/Entity Type

Music Download

Contact Information for Business Card

Cel (318) 4207265518 www.lumadrift.com

Requirements
Must have
• open mind
Nice to have
• open mind
Should not have
• DJ

```html
<!DOCTYPE html>
<html lang="en">
<head>
<meta charset="UTF-8">
<title>Luma Business Card</title>
<link href="https://fonts.googleapis.com/css2?family=Source+Sans+3:wght@400;600;700;900&display=swap" rel="stylesheet">
<style>
  :root {
    --backdrop: #6b6b6b;
    --card-light: #f3f3f3;
    --card-dark: #2a2928;
    --ink-dark: #2a2928;
    --ink-body: #333333;
    --ink-light: #d0d0d2;
    --ink-white: #f2f2f2;
  }
  * { margin: 0; padding: 0; box-sizing: border-box; }
  html, body { width: 1200px; height: 900px; overflow: hidden; }
  body {
    background: var(--backdrop);
    font-family: "Source Sans 3", "Myriad Pro", sans-serif;
    position: relative;
  }
  .card {
    position: absolute;
    top: 184px;
    height: 491px;
    border-radius: 12px;
    text-align: center;
  }
  .card--front { left: 299px; width: 301px; background: var(--card-light); color: var(--ink-body); }
  .card--back { left: 645px; width: 305px; background: var(--card-dark); }

  .brand {
    position: absolute;
    left: 0; right: 0;
    font-weight: 900;
    font-size: 82px;
    line-height: 82px;
    letter-spacing: 2px;
  }
  .card--front .brand { top: 56px; color: var(--ink-dark); }
  .card--back .brand { top: 291px; color: var(--ink-light); }

  .holder { position: absolute; top: 268px; left: 0; right: 0; }
  .holder__name { font-size: 20px; font-weight: 600; color: var(--ink-dark); line-height: 24px; }
  .holder__role { font-size: 15px; line-height: 20px; }

  .contacts { position: absolute; top: 341px; left: 0; right: 0; font-size: 15px; line-height: 20px; }
  .contacts__item { display: flex; justify-content: center; align-items: center; gap: 8px; }
  .contacts__icon { width: 11px; height: 11px; fill: var(--ink-dark); }

  .address { position: absolute; top: 420px; left: 0; right: 0; font-size: 15px; line-height: 16px; }

  .website {
    position: absolute; top: 434px; left: 0; right: 0;
    font-size: 15px; font-weight: 600; color: var(--ink-white);
  }
</style>
</head>
<body>
  <section class="card card--front">
    <div class="brand">LUMA</div>
    <div class="holder">
      <div class="holder__name">JOHN SMITH</div>
      <div class="holder__role">Managing Direcator</div>
    </div>
    <div class="contacts">
      <div class="contacts__item">
        <svg class="contacts__icon" viewBox="0 0 12 12" aria-hidden="true"><path d="M1 4c0-2 2-3 5-3s5 1 5 3l-2 1-1-2H4L3 5zM2 6h8l1 5H1z"/></svg>
        <span>823-456-7890</span>
      </div>
      <div class="contacts__item">
        <svg class="contacts__icon" viewBox="0 0 12 12" aria-hidden="true"><path d="M1 2h10v8H1z M1 2l5 4 5-4" stroke="#f3f3f3" stroke-width="0.8"/></svg>
        <span>info@youremail.com</span>
      </div>
    </div>
    <div class="address">
      <div>1234, Address Goes Here</div>
      <div>Country Name, 123456</div>
    </div>
  </section>

  <section class="card card--back">
    <div class="brand">LUMA</div>
    <div class="website">www.lumadrift.com</div>
  </section>
</body>
</html>
```